I am looking for a modern, clean and neat design for a reflexology and well being business. The business name is Gralo Tund (this is an old Latin word for wellbeing). The colours I would like are purple, white and grey. I am open to suggestions for pictures such as healing or working hands, a pair of feet, images that represent my business that you may think of....... or maybe you think no images at all would be best? My tag line is: "Relax, Renew, Revive" or "Find you balance......... Relax, Renew, Revive" I can decide which I want so I would like to see what both would look like. I would like space on the back to write the client's appointment date and time (more than once)

```html
<!DOCTYPE html>
<html lang="en">
<head>
<meta charset="utf-8">
<title>Gralo Tund – Business Card</title>
<link href="https://fonts.googleapis.com/css2?family=Open+Sans:wght@400;600;700&display=swap" rel="stylesheet">
<style>
  :root{
    --periwinkle:#a2b9e0;
    --white:#ffffff;
    --charcoal:#4a4a4c;
    --stage:#e9ebef;
    --dots:rgba(255,255,255,.85);
  }
  *{box-sizing:border-box;margin:0;padding:0}
  html,body{width:1200px;height:900px;overflow:hidden}
  body{background:var(--stage);font-family:"Open Sans",Arial,sans-serif;position:relative}

  .card{position:absolute;width:560px;height:320px;border-radius:22px;overflow:hidden;
        box-shadow:0 10px 30px rgba(0,0,0,.18)}

  /* Back: appointment side */
  .card-back{left:60px;top:110px;background:var(--periwinkle);color:var(--white)}
  .card-back .tagline{position:absolute;right:40px;top:40px;font-size:13px;font-weight:600;letter-spacing:.5px}
  .card-back .brand{position:absolute;right:40px;top:70px;display:flex;align-items:center;gap:10px;
        font-size:22px;font-weight:600}
  .card-back .brand-dot{width:26px;height:26px;border-radius:50%;background:var(--white)}
  .appointment{position:absolute;left:36px;top:150px;width:420px}
  .appointment h2{font-size:18px;font-weight:700;margin-bottom:12px}
  .appointment .row{display:flex;align-items:flex-end;font-size:13px;margin-bottom:14px}
  .appointment .line{flex:1;border-bottom:2px dotted var(--dots);margin-left:4px;height:1px}

  /* Front: contact side */
  .card-front{left:580px;top:470px;background:var(--white);color:var(--charcoal)}
  .card-front .brand{position:absolute;right:40px;top:60px;display:flex;align-items:center;gap:12px;
        font-size:28px;font-weight:400;letter-spacing:1px;text-transform:uppercase}
  .card-front .brand-dot{width:30px;height:30px;border-radius:50%;background:var(--periwinkle)}
  .name-band{position:absolute;left:300px;right:0;top:150px;height:56px;background:var(--periwinkle);
        padding:8px 30px 0 0;text-align:right}
  .name-band .person{color:var(--white);font-size:20px;font-weight:700;letter-spacing:1px;line-height:1.1}
  .name-band .role{color:var(--charcoal);font-size:11px;font-weight:600;letter-spacing:.5px}
  .contact-band{position:absolute;left:150px;width:300px;top:206px;height:66px;background:var(--periwinkle);
        padding:6px 0 0 30px;color:var(--white);font-size:13px;line-height:19px}
  .contact-band li{list-style:none;display:flex;align-items:center;gap:8px}
  .contact-band svg{width:11px;height:11px;flex:none}
  .corner-mark{position:absolute;left:82px;top:196px;width:100px;height:100px;border-radius:50%;
        background:var(--periwinkle)}
</style>
</head>
<body>

<section class="card card-back" aria-label="Appointment side">
  <p class="tagline">RELAX, RENEW, REVIVE</p>
  <div class="brand"><span class="brand-dot"></span>Gralo Tund</div>
  <div class="appointment">
    <h2>Appointment:</h2>
    <div class="row">Name:<span class="line"></span></div>
    <div class="row">Time:<span class="line"></span></div>
    <div class="row">Date:<span class="line"></span></div>
  </div>
</section>

<section class="card card-front" aria-label="Contact side">
  <div class="brand"><span class="brand-dot"></span>Gralo Tund</div>
  <div class="name-band">
    <p class="person">MARA VELDE</p>
    <p class="role">DIRECTOR</p>
  </div>
  <div class="corner-mark"></div>
  <ul class="contact-band">
    <li><svg viewBox="0 0 12 12"><path fill="#4a4a4c" d="M2.5 1l2 2.2-1 1.3a6 6 0 0 0 4 4l1.3-1 2.2 2-1.2 1.5C5 11 1 7 1 2.2z"/></svg>+44 1632 960 418</li>
    <li><svg viewBox="0 0 12 12"><rect x="1" y="2.5" width="10" height="7" fill="none" stroke="#4a4a4c" stroke-width="1.3"/><path d="M1 2.5l5 4 5-4" fill="none" stroke="#4a4a4c" stroke-width="1.3"/></svg>info@gralotund.com</li>
    <li><svg viewBox="0 0 12 12"><circle cx="6" cy="6" r="5" fill="none" stroke="#4a4a4c" stroke-width="1.3"/><path d="M1 6h10M6 1c-2.5 3-2.5 7 0 10M6 1c2.5 3 2.5 7 0 10" fill="none" stroke="#4a4a4c" stroke-width="1"/></svg>www.gralotund.com</li>
  </ul>
</section>

</body>
</html>
```